Redesign business cards

We have a new logo and I am not that happy with the layout of our existing card and looking for a change. Font is a bit small and the green can be hard to read. Logo may need a tidy up as the copy I have is not that hi-res too so require you to produce a hi-res version of the logo for us too. There will be three individual business cards to produce with just the names and phone numbers being different. Address will change too, but use what you see on the card for now.

Industry/Entity Type

Business

Requirements
Nice to have
• You could consider a redesign to the new logo, just not too radical. We like the blue and green hexagons as we feel that they are representative of oil industry that we are in.

```html
<!DOCTYPE html>
<html lang="en">
<head>
<meta charset="utf-8">
<title>Verdale Fuel Services – Business Cards</title>
<link href="https://fonts.googleapis.com/css2?family=Open+Sans:wght@400;600;700&display=swap" rel="stylesheet">
<style>
  :root {
    --bg: #9a9c9e;
    --card: #ffffff;
    --green: #8cc63f;
    --green-dark: #76b22e;
    --grey-text: #5b5d60;
    --swoosh: #c9cacc;
    --swoosh-dark: #6d6f72;
    --accent: #f5911e;
  }
  * { box-sizing: border-box; margin: 0; padding: 0; }
  html, body { width: 1200px; height: 772px; overflow: hidden; }
  body {
    background: var(--bg);
    font-family: "Open Sans", Arial, sans-serif;
    position: relative;
  }
  .card {
    position: absolute;
    top: 231px;
    width: 540px;
    height: 310px;
    background: var(--card);
    overflow: hidden;
    box-shadow: 0 4px 14px rgba(0,0,0,0.25);
  }
  .card--back { left: 40px; }
  .card--front { left: 620px; }

  .brand { display: flex; align-items: center; gap: 14px; }
  .brand__mark { width: 44px; height: 44px; background: var(--accent); flex: none; }
  .brand__name {
    font-weight: 700;
    color: var(--green);
    font-size: 54px;
    line-height: 1;
    letter-spacing: -1px;
  }
  .brand__tag {
    font-weight: 600;
    color: var(--grey-text);
    font-size: 22px;
    margin-top: 4px;
    margin-left: 58px;
  }

  .card--back .brand-block { position: absolute; left: 70px; top: 100px; }

  .card--front .brand-block { position: absolute; right: 40px; top: 28px; }
  .card--front .brand__mark { width: 30px; height: 30px; }
  .card--front .brand__name { font-size: 38px; }
  .card--front .brand__tag { font-size: 16px; margin-left: 44px; }

  .person { position: absolute; left: 36px; top: 92px; }
  .person__name { color: var(--green-dark); font-weight: 700; font-size: 19px; line-height: 1.3; }
  .person__role { color: var(--grey-text); font-weight: 600; font-size: 15px; margin-top: 2px; }

  .wave { position: absolute; left: 0; top: 0; width: 540px; height: 310px; }

  .contact {
    position: absolute;
    right: 26px;
    bottom: 18px;
    text-align: right;
    color: #ffffff;
    font-size: 12.5px;
    line-height: 1.55;
  }
  .contact__row { display: flex; justify-content: flex-end; align-items: center; gap: 6px; white-space: nowrap; }
  .contact__icon { width: 11px; height: 11px; fill: #ffffff; flex: none; }
  .contact__spacer { width: 11px; height: 11px; flex: none; }
</style>
</head>
<body>

  <section class="card card--back" aria-label="Card back">
    <div class="brand-block">
      <div class="brand">
        <span class="brand__mark"></span>
        <span class="brand__name">Verdale</span>
      </div>
      <div class="brand__tag">Fuel Services</div>
    </div>
  </section>

  <section class="card card--front" aria-label="Card front">
    <svg class="wave" viewBox="0 0 540 310" aria-hidden="true">
      <path d="M0 160 C 200 146, 380 186, 540 146 L540 158 C 380 198, 200 158, 0 172 Z" fill="var(--swoosh)"/>
      <path d="M0 176 C 200 162, 380 202, 540 162 L540 169 C 380 209, 200 169, 0 183 Z" fill="var(--swoosh-dark)"/>
      <path d="M0 187 C 200 173, 380 213, 540 173 L540 310 L0 310 Z" fill="var(--green)"/>
    </svg>

    <div class="brand-block">
      <div class="brand">
        <span class="brand__mark"></span>
        <span class="brand__name">Verdale</span>
      </div>
      <div class="brand__tag">Fuel Services</div>
    </div>

    <div class="person">
      <div class="person__name">Corin Ashby-Lane</div>
      <div class="person__role">Consultant</div>
    </div>

    <div class="contact">
      <div class="contact__row">14 Harbour Row, 3rd Floor
        <svg class="contact__icon" viewBox="0 0 12 12"><path d="M6 0a4 4 0 0 0-4 4c0 3 4 8 4 8s4-5 4-8a4 4 0 0 0-4-4zm0 5.5A1.5 1.5 0 1 1 6 2.5a1.5 1.5 0 0 1 0 3z"/></svg>
      </div>
      <div class="contact__row">Eastfield Road EFR<span class="contact__spacer"></span></div>
      <div class="contact__row">012 555 0147
        <svg class="contact__icon" viewBox="0 0 12 12"><path d="M2.5 0.5l2 2.5-1 1.5a7 7 0 0 0 4 4l1.5-1 2.5 2-1 2C5 11.5 0.5 7 0.5 1.5z"/></svg>
      </div>
      <div class="contact__row">c.ashby@verdalefuel.com
        <svg class="contact__icon" viewBox="0 0 12 12"><path d="M0 2h12v8H0zM1 3l5 4 5-4v-.2H1z"/></svg>
      </div>
      <div class="contact__row">www.verdalefuel.com<span class="contact__spacer"></span></div>
    </div>
  </section>

</body>
</html>
```